Mobile Fitness snd Therapy Business Card Design

I need a business card designed for my mobile fitness and therapy business.

Please view the images that I have uploaded. I like the simplicity of the design that I have attached. I adapted it with my information

Target Market(s)

Those seeking personal training, injury rehabilitation or massage therapy.

Industry/Entity Type

Business

Contact Information for Business Card

Derek Fulham - MSc, CAT(C), RMT, CSCS, Pn2
e-mail: derek@vantrelo.com
website: www.vantrelo.com
instagram: @derek_fulham

Font styles to use
Sans Serif

Colors
3176b5
0355a3

Requirements
Must have
• "Contact us to receive a FREE assessment"
• Services offered:
• Personal Training
• Golf Fitness
• Injury Rehab
• Massage Therapy
• Yoga
Nice to have
• Consistent colours with brand
• - Dark Blue: #232837
• - Blue: #5096f0
• Consistent look/feel with the website: www.vantrelo.com

```html
<!DOCTYPE html>
<html lang="en">
<head>
<meta charset="utf-8">
<title>Vantrelo Business Card</title>
<link href="https://fonts.googleapis.com/css2?family=Roboto:wght@400;500;700&family=Roboto+Condensed:wght@400;700&display=swap" rel="stylesheet">
<style>
  :root {
    --stage: #e4e2df;
    --card-front: #f4f4f4;
    --navy: #232837;
    --brand-blue: #2f5fd0;
    --pill-blue: #2c59d2;
    --ink: #1f2430;
    --muted: #4a4d55;
    --white: #ffffff;
  }
  * { margin: 0; padding: 0; box-sizing: border-box; }
  html, body { width: 1200px; height: 960px; overflow: hidden; }
  body {
    background: var(--stage);
    position: relative;
    font-family: "Roboto", Arial, sans-serif;
  }
  .card {
    position: absolute;
    width: 600px;
    height: 343px;
    border-radius: 22px;
    box-shadow: 0 3px 8px rgba(0,0,0,0.25);
    overflow: hidden;
  }
  .card-front { left: 314px; top: 113px; background: var(--card-front); }
  .card-back { left: 312px; top: 472px; background: var(--navy); }

  .brand-name {
    font-family: "Roboto", Arial, sans-serif;
    font-weight: 700;
    letter-spacing: 3px;
    line-height: 1;
  }
  .brand-tagline {
    font-weight: 700;
    letter-spacing: 2px;
    line-height: 1;
  }
  .front-brand {
    position: absolute;
    right: 36px;
    top: 38px;
    text-align: right;
  }
  .front-brand .brand-name { font-size: 36px; color: var(--ink); }
  .front-brand .brand-tagline { font-size: 11px; color: var(--ink); margin-top: 8px; }

  .person {
    position: absolute;
    left: 37px;
    top: 191px;
  }
  .person-name {
    font-family: "Roboto Condensed", Arial, sans-serif;
    font-weight: 700;
    font-size: 22px;
    color: var(--brand-blue);
    line-height: 1;
  }
  .person-credentials {
    font-family: "Roboto Condensed", Arial, sans-serif;
    font-weight: 700;
    font-size: 11px;
    color: var(--brand-blue);
    margin-top: 4px;
  }
  .contact-list {
    position: absolute;
    left: 37px;
    top: 247px;
    list-style: none;
  }
  .contact-item {
    display: flex;
    align-items: center;
    height: 19px;
    font-size: 14px;
    color: var(--muted);
  }
  .contact-icon { width: 14px; height: 14px; margin-right: 9px; flex: none; }

  .back-pattern {
    position: absolute;
    inset: 0;
    background: linear-gradient(180deg, #252c3f 0%, #232837 100%);
  }
  .back-brand {
    position: absolute;
    left: 0; right: 0;
    top: 118px;
    text-align: center;
  }
  .back-brand .brand-name { font-size: 48px; color: var(--white); letter-spacing: 5px; }
  .back-brand .brand-tagline { font-size: 15px; color: var(--white); margin-top: 14px; letter-spacing: 2.5px; }

  .cta {
    position: absolute;
    left: 57px;
    top: 257px;
    width: 483px;
    height: 33px;
    border-radius: 17px;
    background: var(--pill-blue);
    color: var(--white);
    font-family: "Roboto Condensed", Arial, sans-serif;
    font-weight: 700;
    font-size: 20px;
    display: flex;
    align-items: center;
    justify-content: center;
  }
  .services {
    position: absolute;
    left: 0; right: 0;
    top: 297px;
    text-align: center;
    font-size: 14.5px;
    color: var(--white);
  }
  .services .sep { color: #7d8398; margin: 0 4px; }
</style>
</head>
<body>

  <section class="card card-front">
    <div class="front-brand">
      <div class="brand-name">VANTRELO</div>
      <div class="brand-tagline">NUTRITION - FITNESS - HEALTH</div>
    </div>

    <div class="person">
      <div class="person-name">DEREK FULHAM</div>
      <div class="person-credentials">MSC, CAT(C), RMT, CSCS, PN2</div>
    </div>

    <ul class="contact-list">
      <li class="contact-item">
        <svg class="contact-icon" viewBox="0 0 14 14"><rect x="1" y="3" width="12" height="8" fill="var(--brand-blue)"/><path d="M1 3 L7 8 L13 3" fill="none" stroke="#fff" stroke-width="1.2"/></svg>
        derek@vantrelo.com
      </li>
      <li class="contact-item">
        <svg class="contact-icon" viewBox="0 0 14 14"><circle cx="7" cy="7" r="6" fill="var(--brand-blue)"/></svg>
        www.vantrelo.com
      </li>
      <li class="contact-item">
        <svg class="contact-icon" viewBox="0 0 14 14"><circle cx="7" cy="7" r="6" fill="var(--brand-blue)"/></svg>
        @derek_fulham
      </li>
    </ul>
  </section>

  <section class="card card-back">
    <div class="back-pattern" role="img" aria-label="Subtle repeating vertical bar pattern in dark blue tones"></div>
    <div class="back-brand">
      <div class="brand-name">VANTRELO</div>
      <div class="brand-tagline">NUTRITION - FITNESS - HEALTH</div>
    </div>
    <div class="cta">CONTACT US TO RECEIVE A FREE ASSESSMENT</div>
    <div class="services">
      Personal Training<span class="sep">|</span>Golf Fitness<span class="sep">|</span>Injury Rehab<span class="sep">|</span>Massage Therapy<span class="sep">|</span>Yoga
    </div>
  </section>

</body>
</html>
```